Brell Stone Company Business Cards

Front and Back Business Card - logo and text setup - cool design. I need workable photoshop or illustrator files so I can setup each employee card with design that is created
Updates

Hi everyone, thank you for the great entries. Please no more white and blue cards - there are so many already - black and silver only now please. thanks!

Target Market(s)

Construction Industry - Facility Managers

Industry/Entity Type

Construction

Contact Information for Business Card

I really like contemporary simplistic looks - clean neat....not opposed to seeing some black backrounds

Requirements
Must have
• Logo/website address with design on front only - www.brellstone-example.com (logo attached)
• Back:
• Name/Title/Company Address/Phone/email address
Nice to have
• Cool design
Should not have
• Nothing gimmicky like Fire or Water - since we are a Fire Protection company - it has all been done

```html
<!DOCTYPE html>
<html lang="en">
<head>
<meta charset="utf-8">
<title>Brell Stone Company — Business Card</title>
<link href="https://fonts.googleapis.com/css2?family=Lato:wght@400;700;900&display=swap" rel="stylesheet">
<style>
  :root {
    --backdrop: #575757;
    --silver-light: #f1f2f4;
    --silver: #d3d6da;
    --silver-mid: #9da2a8;
    --silver-dark: #6f747a;
    --black: #141414;
    --charcoal: #2b2c2e;
    --ink-grey: #3c3e41;
  }
  html, body {
    margin: 0;
    padding: 0;
    overflow: hidden;
  }
  body {
    width: 1200px;
    height: 900px;
    background: var(--backdrop);
    position: relative;
    font-family: "Lato", Arial, sans-serif;
  }
  .card {
    position: absolute;
    top: 200px;
    width: 310px;
    height: 502px;
    box-shadow: 3px 4px 6px rgba(0, 0, 0, 0.45);
    box-sizing: border-box;
  }
  .card-front {
    left: 253px;
    background: linear-gradient(160deg, var(--silver-light) 0%, #e2e4e7 55%, var(--silver) 100%);
    border-radius: 62px 0 62px 0;
  }
  .card-back {
    left: 627px;
    background: linear-gradient(205deg, var(--charcoal) 0%, #1d1e20 50%, var(--black) 100%);
    border-radius: 0 62px 0 62px;
  }
  .wordmark {
    position: absolute;
    font-weight: 900;
    letter-spacing: -0.5px;
    line-height: 1;
    white-space: nowrap;
  }
  .wordmark small {
    display: block;
    text-align: right;
    font-size: 24px;
    margin-top: 0;
  }
  .card-front .wordmark {
    left: 32px;
    top: 138px;
    font-size: 56px;
    color: var(--black);
  }
  .card-back .wordmark {
    left: 28px;
    top: 212px;
    width: 256px;
    font-size: 58px;
    color: var(--silver);
    text-align: center;
  }
  .contact {
    position: absolute;
    left: 32px;
    top: 334px;
    color: var(--ink-grey);
    font-size: 15px;
    line-height: 1.25;
  }
  .contact p { margin: 0; }
  .contact-name {
    font-size: 19px;
    font-weight: 700;
    color: var(--black);
    line-height: 1.1;
    letter-spacing: 0.2px;
  }
  .contact-name .surname { color: var(--silver-dark); }
  .contact .contact-title { margin: 1px 0 5px; }
  .contact .contact-line {
    display: flex;
    align-items: center;
    gap: 5px;
    margin-bottom: 1px;
  }
  .contact-line svg { width: 11px; height: 11px; fill: var(--black); }
  .contact .contact-address { margin: 6px 0 0 2px; line-height: 1.3; }
  .website {
    position: absolute;
    left: 0;
    right: 0;
    top: 438px;
    text-align: center;
    color: var(--silver);
    font-size: 15px;
  }
</style>
</head>
<body>
  <section class="card card-front" aria-label="Card front">
    <div class="wordmark">brellstone<small>inc.</small></div>
    <div class="contact">
      <p class="contact-name">MARCUS <span class="surname">HALE</span></p>
      <p class="contact-title">Managing Director</p>
      <p class="contact-line">
        <svg viewBox="0 0 12 12" aria-hidden="true"><path d="M1 4c0-2 2-3 5-3s5 1 5 3v1H8V4H4v1H1z M2 6h8l1 5H1z"/></svg>
        044-555 018 274
      </p>
      <p class="contact-line">
        <svg viewBox="0 0 12 12" aria-hidden="true"><path d="M1 2h10v8H1z"/><path d="M1.5 2.5 6 6.5l4.5-4" stroke="#e2e4e7" stroke-width="1" fill="none"/></svg>
        info@brellstone-example.com
      </p>
      <p class="contact-address">421, Address line here,<br>45452,Country Name</p>
    </div>
  </section>

  <section class="card card-back" aria-label="Card back">
    <div class="wordmark">brellstone<small>inc.</small></div>
    <div class="website">www.brellstone-example.com</div>
  </section>
</body>
</html>
```